Business Card Design Project

Looking for a logo and business card for a Real State Business i will be opening. The name is not choosen yet , but will probably be RWT IMOVEIS.
I was thinking black and silver colors, but am open to nice ideas.
I did add a business card that i liked a lot, am looking for something like that, with logo in black or silver in a black card. The logo i was thinking in the letters RWT as i uploaded or something or little and cute buildings or a house...just ideas, can be any nice logo.
Updates

You guys can add other colors if you want, I like colors very "BRIGHT" and "open", like red, pink, strong colors. almost glow in the dark colors. lol

Designers,

I've increased more 88 dollars in the budget for 1st place cause I will want envelope designs... small and big sizes.

So 1st place is now U$248,00. 

No need to send the envelope designs right now... only the business cards designs.

Thank you.

Industry/Entity Type

Business

Requirements
Must have
• Marcela Tavares Rocha

www.RWTimoveis-exemplo.com.br

+554187316042

marcela@rwtimoveis-exemplo.com.br

```html
<!DOCTYPE html>
<html lang="pt-BR">
<head>
<meta charset="utf-8">
<title>RWT Imóveis – Cartão de visita</title>
<link rel="stylesheet" href="https://fonts.googleapis.com/css2?family=Michroma&display=swap">
<style>
  :root {
    --backdrop: #d4d4d4;
    --card: #151515;
    --silver: #e8e8e8;
    --silver-soft: #cfcfcf;
    --band-light: #bdbdbd;
    --band-dark: #7a7a7a;
  }
  * { margin: 0; padding: 0; box-sizing: border-box; }
  html, body {
    width: 1200px;
    height: 900px;
    overflow: hidden;
    background: var(--backdrop);
  }
  .stage {
    position: relative;
    width: 1200px;
    height: 900px;
    font-family: "Michroma", "Arial", sans-serif;
    color: var(--silver);
  }
  .card {
    position: absolute;
    width: 600px;
    height: 340px;
    left: 300px;
    background: var(--card);
    box-shadow: 0 10px 24px rgba(0,0,0,0.25);
    overflow: hidden;
  }
  .card--back { top: 70px; }
  .card--front { top: 490px; }

  /* Back side: content runs vertically, reading bottom to top */
  .back-content {
    position: absolute;
    width: 340px;
    height: 600px;
    left: 130px;
    top: -130px;
    transform: rotate(-90deg);
  }
  .back-brand {
    position: absolute;
    left: 36px;
    top: 112px;
    display: flex;
    align-items: center;
    gap: 10px;
    font-size: 22px;
    letter-spacing: 1px;
    white-space: nowrap;
  }
  .brand-square {
    width: 16px;
    height: 16px;
    background: var(--silver);
    flex: none;
  }
  .pattern-band {
    position: absolute;
    left: 0;
    top: 250px;
    width: 340px;
    height: 72px;
    background: linear-gradient(90deg, var(--band-dark), var(--band-light) 50%, var(--band-dark));
  }
  .contact {
    position: absolute;
    left: 34px;
    top: 392px;
    display: flex;
    flex-direction: column;
    gap: 9px;
    text-transform: uppercase;
    white-space: nowrap;
  }
  .contact__name {
    font-size: 12px;
    letter-spacing: 1.6px;
    margin-bottom: 16px;
  }
  .contact__line {
    font-size: 8px;
    letter-spacing: 0.6px;
    color: var(--silver-soft);
  }
  .contact__phone { font-size: 9px; letter-spacing: 2.5px; }

  /* Front side */
  .front-brand {
    position: absolute;
    left: 0;
    right: 0;
    top: 0;
    bottom: 0;
    display: flex;
    align-items: center;
    justify-content: center;
    gap: 16px;
    font-size: 40px;
    letter-spacing: 2px;
    padding-top: 40px;
    white-space: nowrap;
  }
  .front-brand .brand-square {
    width: 26px;
    height: 26px;
  }
</style>
</head>
<body>
  <main class="stage">
    <section class="card card--back" aria-label="Verso do cartão">
      <div class="back-content">
        <div class="back-brand"><span class="brand-square"></span><span>RWT IMÓVEIS</span></div>
        <div class="pattern-band" role="img" aria-label="Faixa decorativa de quadradinhos prateados"></div>
        <div class="contact">
          <p class="contact__name">Marcela Tavares Rocha</p>
          <p class="contact__line contact__phone">41 8731 6042</p>
          <p class="contact__line">marcela@rwtimoveis-exemplo.com.br</p>
          <p class="contact__line">www.rwtimoveis-exemplo.com.br</p>
        </div>
      </div>
    </section>

    <section class="card card--front" aria-label="Frente do cartão">
      <div class="front-brand"><span class="brand-square"></span><span>RWT IMÓVEIS</span></div>
    </section>
  </main>
</body>
</html>
```